Bry7Legal Letterhead

Need a new letterhead for my law firm.
IDENTIFYING INFORMATION BELOW:
Anselmo R Quintara III
Attorney at Law
Address: 2847 Larkspur Blvd, Ste 300, Dallas, TX 75204
Phone: 877-482-6017
Fax: 469-738-1452
Email: bry@bry7legal.example
Website: www.bry7legal.example

Colors
0054AA
0677BA
7BADD7
CADEEF
E8F1F8

Requirements
Must have
• Logo needs to be on the letterhead, along with identifying information which is included in the project description.

```html
<!DOCTYPE html>
<html lang="en">
<head>
<meta charset="utf-8">
<title>Bry7Legal Letterhead</title>
<link href="https://fonts.googleapis.com/css2?family=Montserrat:wght@400;500;700;800&display=swap" rel="stylesheet">
<style>
  :root {
    --brand-navy: #0a3f80;
    --brand-blue: #0054AA;
    --brand-mid: #0677BA;
    --brand-light: #1a8fd0;
    --ink: #1a1a1a;
    --paper: #ffffff;
    --backdrop: #c9ccd0;
  }
  * { margin: 0; padding: 0; box-sizing: border-box; }
  html, body { width: 1200px; height: 1200px; overflow: hidden; }
  body {
    background: var(--backdrop);
    font-family: "Montserrat", sans-serif;
    color: var(--ink);
    position: relative;
  }
  .letterhead {
    position: absolute;
    left: 205px; top: 41px;
    width: 790px; height: 1118px;
    background: var(--paper);
  }
  .brand { position: absolute; left: 53px; top: 80px; width: 308px; text-align: center; }
  .brand-name {
    font-weight: 800; font-size: 44px; letter-spacing: 1px;
    color: var(--ink); line-height: 44px; text-transform: uppercase;
  }
  .brand-tagline {
    font-weight: 400; font-size: 17px; letter-spacing: 3.4px;
    margin-top: 4px; color: var(--ink);
  }
  .contact-person { position: absolute; left: 418px; top: 80px; font-size: 11.5px; line-height: 15px; }
  .contact-person .name { color: var(--brand-blue); font-weight: 700; font-size: 12.5px; margin-bottom: 1px; }
  .contact-person .label { color: var(--brand-mid); }
  .contact-person .title { margin-bottom: 3px; }
  .contact-lines { position: absolute; left: 614px; top: 80px; font-size: 11.5px; line-height: 16.4px; list-style: none; }
  .contact-lines li { display: flex; align-items: center; gap: 5px; white-space: nowrap; }
  .contact-lines svg { width: 10px; height: 10px; fill: var(--brand-mid); flex: none; }
  .header-band {
    position: absolute; left: 53px; top: 216px; width: 687px; height: 13px;
    background: linear-gradient(90deg, var(--brand-navy) 0%, var(--brand-mid) 20%, var(--brand-light) 50%, var(--brand-mid) 80%, var(--brand-navy) 92%, var(--brand-navy) 100%);
  }
  .letter-body { position: absolute; left: 53px; top: 279px; width: 687px; }
  .salutation { color: var(--brand-mid); font-weight: 700; font-size: 14px; letter-spacing: 0.3px; margin-bottom: 20px; }
  .letter-body p {
    font-size: 11.9px; line-height: 19px; text-align: justify; letter-spacing: 0.25px;
    margin-bottom: 38px; hyphens: auto;
  }
  .signature { position: absolute; left: 53px; top: 890px; font-size: 11.5px; line-height: 15px; }
  .signature .rule { width: 148px; border-top: 1.5px dotted var(--ink); margin-bottom: 8px; }
  .signature .name { color: var(--brand-blue); font-weight: 700; font-size: 12.5px; }
</style>
</head>
<body>
  <main class="letterhead">
    <header>
      <div class="brand">
        <div class="brand-name">Bry7Legal</div>
        <div class="brand-tagline">BUILT ON TRUST</div>
      </div>
      <div class="contact-person">
        <div class="name">Anselmo R Quintara III</div>
        <div class="title">Attorney at Law</div>
        <div><span class="label">Address:</span> 2847 Larkspur Blvd,</div>
        <div>Ste 300, Dallas, TX 75204</div>
      </div>
      <ul class="contact-lines">
        <li><svg viewBox="0 0 10 10"><path d="M2 0.5l1.6 2.2-1 1a6 6 0 0 0 3.7 3.7l1-1L9.5 8 8.3 9.5C4 9.5 0.5 6 0.5 1.7z"/></svg>877-482-6017</li>
        <li><svg viewBox="0 0 10 10"><rect x="2.5" y="0.5" width="5" height="3"/><rect x="0.5" y="3.5" width="9" height="4" rx="1"/><rect x="2.5" y="6.5" width="5" height="3"/></svg>469-738-1452</li>
        <li><svg viewBox="0 0 10 10"><path d="M0.5 2h9v0.6L5 5.6 0.5 2.6z"/><path d="M0.5 3.6L5 6.6l4.5-3V8.5h-9z"/></svg>bry@bry7legal.example</li>
        <li><svg viewBox="0 0 10 10"><circle cx="5" cy="5" r="4.2" fill="none" stroke="#0677BA" stroke-width="1.2"/><path d="M3 3.5l2-1 1 1.5-1.5 1 0.5 2-2-1.5z"/></svg>www.bry7legal.example</li>
      </ul>
    </header>

    <div class="header-band"></div>

    <section class="letter-body">
      <div class="salutation">Dear Jhon,</div>
      <p>Contrary to popular belief, Lorem Ipsum is not simply random text. It has roots in a piece of classical Latin literature from 45 BC, making it over 2000 years old. Walter Penhallow, a Latin professor at Aldermoor College in Virginia, looked up one of the more obscure Latin words, consectetur, from a Lorem Ipsum passage, and going through the cites of the word in classical literature, discovered the undoubtable source.</p>
      <p>There are many variations of passages of Lorem Ipsum available, but the majority have suffered alteration in some form, by injected humour, or randomised words which don't look even slightly believable. If you are going to use a passage of Lorem Ipsum, you need to be sure there isn't anything embarrassing hidden in the middle of text. All the Lorem Ipsum generators on the Internet tend to repeat predefined chunks as necessary, making this the first true generator on the Internet. It uses a dictionary of over 200 Latin words, combined with a handful of model sentence structures, to generate Lorem Ipsum which looks reasonable. The generated Lorem Ipsum is therefore always free from repetition, injected humour, or non-characteristic words etc..</p>
      <p>It is a long established fact that a reader will be distracted by the readable content of a page when looking at its layout. The point of using Lorem Ipsum is that it has a more-or-less normal distribution of letters, as opposed to using 'Content here, content here', making it look like readable English. Many desktop publishing packages and web page editors now use Lorem Ipsum as their default model text, and a search for 'lorem ipsum' will uncover many web sites still in their infancy. Various versions have evolved over the years, sometimes by accident, sometimes on purpose (injected humour and the like).</p>
    </section>

    <footer class="signature">
      <div class="rule"></div>
      <div class="name">Anselmo R Quintara III</div>
      <div>Attorney at Law</div>
    </footer>
  </main>
</body>
</html>
```